Dalvick's Business Card

I need some designs for a new business card including the new logo attached. An old example of our business card is also attached to show all the data that should be included on the new design.
**I added some more examples someone had mocked up**

Contact Information for Business Card

Should include all info on other examples uploaded.

```html
<!DOCTYPE html>
<html lang="en">
<head>
<meta charset="utf-8">
<title>Dalvick's Business Card</title>
<link href="https://fonts.googleapis.com/css2?family=Montserrat:wght@400;600;700&family=Oswald:wght@500&display=swap" rel="stylesheet">
<style>
  :root {
    --backdrop: #ababab;
    --card: #ffffff;
    --brand-blue: #0a6fba;
    --brand-red: #e8262c;
    --text-grey: #666666;
    --tag-grey: #555555;
    --rule: #d4d4d4;
  }
  * { box-sizing: border-box; margin: 0; padding: 0; }
  html, body { width: 1200px; height: 1000px; overflow: hidden; }
  body { background: var(--backdrop); position: relative; font-family: "Montserrat", sans-serif; }

  .card {
    position: absolute;
    width: 613px;
    height: 351px;
    background: var(--card);
    border-radius: 24px;
    overflow: hidden;
  }
  .card--back { left: 536px; top: 96px; }
  .card--front { left: 90px; top: 526px; }

  .feature-art {
    position: absolute;
    left: 0; top: 0;
    width: 320px; height: 351px;
    background: linear-gradient(100deg, rgba(232, 38, 44, 0.85) 0%, rgba(232, 38, 44, 0.55) 30%, rgba(10, 111, 186, 0.55) 60%, rgba(10, 111, 186, 0.85) 100%);
  }

  .brand {
    position: absolute;
    display: flex;
    align-items: center;
    gap: 8px;
  }
  .brand__dot {
    width: 34px; height: 34px;
    border-radius: 50%;
    background: var(--brand-blue);
    flex: none;
  }
  .brand__text { display: flex; flex-direction: column; }
  .brand__name {
    font-weight: 700;
    font-size: 27px;
    line-height: 28px;
    color: var(--brand-blue);
    letter-spacing: 0.3px;
  }
  .brand__service {
    font-weight: 700;
    font-size: 7.6px;
    line-height: 10px;
    color: var(--brand-red);
    letter-spacing: 0.1px;
    text-transform: uppercase;
    white-space: nowrap;
  }
  .card--back .brand { left: 338px; top: 172px; }
  .card--front .brand { left: 38px; top: 50px; }

  .credentials {
    position: absolute;
    font-family: "Oswald", sans-serif;
    font-weight: 500;
    font-size: 13px;
    line-height: 19px;
    letter-spacing: 1.3px;
    color: var(--tag-grey);
    text-align: center;
    text-transform: uppercase;
    transform: rotate(-5deg);
    white-space: nowrap;
  }
  .card--back .credentials { left: 378px; top: 240px; }
  .card--front .credentials { left: 369px; top: 44px; }

  .person { position: absolute; left: 36px; top: 172px; }
  .person__name { font-weight: 600; font-size: 24px; color: var(--brand-blue); line-height: 30px; }
  .person__role { font-size: 12px; color: var(--brand-red); line-height: 14px; }

  .divider {
    position: absolute;
    left: 37px; top: 242px;
    width: 527px; height: 2px;
    background: var(--rule);
  }

  .contact {
    position: absolute;
    top: 270px;
    font-size: 17px;
    line-height: 23px;
    letter-spacing: 0.8px;
    color: var(--text-grey);
    font-style: normal;
  }
  .contact--direct { left: 35px; }
  .contact--address { left: 339px; top: 272px; }
</style>
</head>
<body>
  <section class="card card--back" aria-label="Card back">
    <div class="feature-art" role="img" aria-label="Large red and blue brand symbol decoration"></div>
    <div class="brand">
      <span class="brand__dot"></span>
      <span class="brand__text">
        <span class="brand__name">DALVICK'S</span>
        <span class="brand__service">Air Conditioning &amp; Heating Service</span>
      </span>
    </div>
    <p class="credentials">Licensed &amp; Insured<br>Family Owned &amp; Operated</p>
  </section>

  <section class="card card--front" aria-label="Card front">
    <div class="brand">
      <span class="brand__dot"></span>
      <span class="brand__text">
        <span class="brand__name">DALVICK'S</span>
        <span class="brand__service">Air Conditioning &amp; Heating Service</span>
      </span>
    </div>
    <p class="credentials">Licensed &amp; Insured<br>Family Owned &amp; Operated</p>

    <div class="person">
      <p class="person__name">Evan Marsh</p>
      <p class="person__role">CEO</p>
    </div>

    <div class="divider"></div>

    <address class="contact contact--direct">
      555.014.2290<br>
      hvacdalvick@example.com
    </address>
    <address class="contact contact--address">
      418 Birchwood Lane<br>
      Millbrook, IA 50123, EUA
    </address>
  </section>
</body>
</html>
```